Veterinary Hospital Business Card

We have recently updated our logo and wish to have a business card designed incorporating the new look and flow. We are a full service veterinary hospital also offering laser therapy, boarding, and grooming. Our website is www.marlowpawsvets.com

Industry/Entity Type

Veterinary

```html
<!DOCTYPE html>
<html lang="en">
<head>
<meta charset="utf-8">
<title>Marlow Paws Animal Hospital – Business Card</title>
<link rel="stylesheet" href="https://fonts.googleapis.com/css2?family=Saira:wght@400;500;700&display=swap">
<style>
  :root {
    --page: #ececec;
    --frame: #a8a9ab;
    --paper: #ffffff;
    --brand: #3f6d87;
    --ink: #2f3a42;
    --head-dark: #3d5f72;
    --head-mid: #6a8fa2;
    --body-deep: #45789a;
    --body-light: #7fa9c0;
    --rule: #ffffff;
  }
  * { box-sizing: border-box; margin: 0; padding: 0; }
  html, body { width: 1200px; height: 786px; overflow: hidden; }
  body {
    background: var(--page);
    font-family: "Saira", "Arial", sans-serif;
    position: relative;
  }
  .card {
    position: absolute;
    width: 540px;
    height: 310px;
    background: var(--frame);
    padding: 14px;
    box-shadow: 0 6px 18px rgba(0,0,0,.18);
  }
  .card--front { left: 40px; top: 238px; }
  .card--back  { left: 620px; top: 238px; }
  .card__inner {
    position: relative;
    width: 100%;
    height: 100%;
    background: var(--paper);
    overflow: hidden;
  }

  /* wordmark */
  .wordmark {
    position: absolute;
    display: flex;
    align-items: center;
    gap: 10px;
    color: var(--brand);
    font-weight: 700;
    text-transform: uppercase;
    line-height: 1;
  }
  .wordmark__dot {
    flex: none;
    border-radius: 50%;
    background: var(--brand);
  }
  .wordmark--front { left: 120px; top: 92px; font-size: 26px; }
  .wordmark--front .wordmark__dot { width: 40px; height: 40px; }
  .wordmark--back { left: 18px; top: 16px; font-size: 13px; gap: 6px; }
  .wordmark--back .wordmark__dot { width: 20px; height: 20px; }
  .wordmark__text span { display: block; }
  .wordmark__text span + span { margin-top: 4px; }

  /* holder */
  .holder {
    position: absolute;
    right: 20px;
    top: 118px;
    text-align: right;
    text-transform: uppercase;
  }
  .holder__name { color: var(--body-deep); font-size: 15px; font-weight: 500; letter-spacing: .5px; }
  .holder__role { color: var(--ink); font-size: 11px; letter-spacing: .8px; margin-top: 1px; }

  /* contact grid */
  .contact { position: absolute; left: 0; right: 0; top: 0; bottom: 0; }
  .contact__col {
    position: absolute;
    bottom: 0;
    width: 170.6px;
    display: flex;
    flex-direction: column;
    border-left: 2px solid var(--rule);
  }
  .contact__col:first-child { border-left: 0; }
  .contact__col--phone { left: 0; top: 104px; }
  .contact__col--web { left: 170.6px; top: 134px; }
  .contact__col--place { left: 341.2px; top: 164px; }
  .contact__head {
    height: 30px;
    display: flex;
    align-items: center;
    justify-content: center;
    border-bottom: 2px solid var(--rule);
  }
  .contact__body {
    flex: 1;
    padding: 16px 14px;
    color: #fff;
    font-size: 10.5px;
    line-height: 1.45;
    letter-spacing: .6px;
  }
  .contact__col--phone .contact__head { background: var(--head-dark); }
  .contact__col--phone .contact__body { background: var(--body-deep); padding-left: 28px; font-size: 11px; }
  .contact__col--web .contact__head { background: var(--head-mid); }
  .contact__col--web .contact__body { background: var(--body-light); padding-top: 40px; font-size: 9.5px; }
  .contact__col--place .contact__head { background: var(--head-dark); }
  .contact__col--place .contact__body { background: var(--body-deep); padding-top: 22px; }
  .icon { width: 20px; height: 20px; }
</style>
</head>
<body>

  <section class="card card--front" aria-label="Business card front">
    <div class="card__inner">
      <div class="wordmark wordmark--front">
        <span class="wordmark__dot"></span>
        <div class="wordmark__text">
          <span>Marlow Paws</span>
          <span>Animal Hospital</span>
        </div>
      </div>
    </div>
  </section>

  <section class="card card--back" aria-label="Business card back">
    <div class="card__inner">
      <div class="wordmark wordmark--back">
        <span class="wordmark__dot"></span>
        <div class="wordmark__text">
          <span>Marlow Paws</span>
          <span>Animal Hospital</span>
        </div>
      </div>

      <div class="holder">
        <p class="holder__name">Daniel Reyes</p>
        <p class="holder__role">General Manager</p>
      </div>

      <div class="contact">
        <div class="contact__col contact__col--phone">
          <div class="contact__head">
            <svg class="icon" viewBox="0 0 20 20" aria-hidden="true">
              <circle cx="10" cy="10" r="8.5" fill="none" stroke="#fff" stroke-width="1.5"/>
              <path d="M7.4 5.6c.5-.3 1-.1 1.2.4l.6 1.5c.1.4 0 .8-.3 1l-.6.5c.4.9 1.2 1.8 2.1 2.3l.5-.6c.3-.3.7-.4 1-.2l1.4.7c.5.2.6.8.3 1.2l-.6.8c-.4.5-1.1.7-1.7.4-2.3-1-4.1-2.9-4.9-5.3-.2-.6 0-1.3.5-1.6z" fill="#fff"/>
            </svg>
          </div>
          <div class="contact__body">
            <p>014 282 5530</p>
            <p>014 282 5531</p>
          </div>
        </div>

        <div class="contact__col contact__col--web">
          <div class="contact__head">
            <svg class="icon" viewBox="0 0 20 20" aria-hidden="true">
              <circle cx="10" cy="10" r="8.5" fill="none" stroke="#fff" stroke-width="1.5"/>
              <circle cx="10" cy="10" r="5" fill="none" stroke="#fff" stroke-width="1.2"/>
              <ellipse cx="10" cy="10" rx="2" ry="5" fill="none" stroke="#fff" stroke-width="1"/>
              <path d="M5 10h10M6 7.5h8M6 12.5h8" stroke="#fff" stroke-width="1"/>
            </svg>
          </div>
          <div class="contact__body">
            <p>hello@marlowpawsvets.com</p>
            <p>www.marlowpawsvets.com</p>
          </div>
        </div>

        <div class="contact__col contact__col--place">
          <div class="contact__head">
            <svg class="icon" viewBox="0 0 20 20" aria-hidden="true">
              <circle cx="10" cy="10" r="8.5" fill="none" stroke="#fff" stroke-width="1.5"/>
              <path d="M10 4.6a3.4 3.4 0 0 1 3.4 3.4c0 2.4-3.4 6.4-3.4 6.4S6.6 10.4 6.6 8A3.4 3.4 0 0 1 10 4.6z" fill="#fff"/>
              <circle cx="10" cy="8" r="1.2" fill="var(--head-dark)"/>
            </svg>
          </div>
          <div class="contact__body">
            <p>214, 3rd floor, Mall</p>
            <p>Harbour Road NVK</p>
          </div>
        </div>
      </div>
    </div>
  </section>

</body>
</html>
```